We need a new website design for our company Brindle Forks (https://www.brindleforks.com/). We DO NOT WANT A BORING STANDARD SITE. This site has to be different, and has to POP!

Logo Files: https://files.examplecloud.net/folders/a7Kq3Lm9Zx2Tp8Rw4Vn6Yb1Hc5Jd0Fs

Website Photos here: https://files.examplecloud.net/folders/b3Wm8Qx_T2ngVr7Lp4Ks9Hd6Zc1Ya0Ej

Websites we like:
https://morvenite.sitebloom.io/
http://crunova.com/

We will need the site building Wordpress/Woocommerce and also help with interior pages & installation plug-ins -- see further attachments.

Information about the company:
1. PURPOSE: Why do we exist?
We believe that food is the root source to healthy living.
2. VISION: What future do we want to help create?
A world of healthy and happy people.
3. MISSION: What are we here to do?
Empower every person to utilize food as a means of living a healthy life.

Value Proposition:
Brindle Forks develops new food based on the latest science to provide the human body with the proper nutrients for optimal health. Our research based foods target the key health functions that support healthy aging and active lifestyles. Since 2002, we have been innovating and designing our meals to meet the needs for healthy aging to active lifestyles. To help people perform their best, today & in the future.

Objective:
This is a nationwide issue and it's coming to the surface. Food affects people in a number of different ways. Our objective is to create an approachable and sustainable solution that can assist people with a number of ailments. The end result for all of them is feeling a feeling they haven't felt in quite some time. Feeling a refreshed you. Like water for fish, food for humans. Keep it clean and simple so you can focus on enjoying your life.

PHRASES/TAGLINES:
Empowerment Through Food
Real Food, Real Results
Nutrition Made Simple
Not Just Meal Prep, Food Science
A healthier you, delivered to your door
Increase your health and wellness baseline.
Discover the potential of healthier eating
Become the best version of you
It’s incredible what proper nutrition feels like
Taste & feel the difference. Your future self will thank you.
A healthier you is just a meal away
Life Changing results
Overwhelmed with being healthy, stops here.
Designed by doctors, approved by humans
Results Driven Healthy Eating, Delivered to you.
Become the person you deserve to be.
Enjoy the process of becoming a better you

Value Propositions:
We Educate & Empower People Through Food to Live Their Best Life
Sustainable health through proper nutrition… that’s enjoyable too.

Key Statements:
We provide satisfying meals that are nutrient dense & deliver results.
Our meals provide an easy way to enjoy an anti-inflammatory diet that's as satisfying as it is healthy.
Health, fat loss & feeling good through chef-prepared, nutrient-dense, satisfying meals delivered to your door.

PLEASE REVIEW THE ATTACHMENTS.

Industry/Entity Type

See Description & Attachments

Coding

Coded - Design and coding required

Number of Pages Required

5+ page

Font styles to use
Other font styles liked:
• See Description & Attachments

Colors
0094D4
00A9DD
6FCCEA
C7EBF8
E9F6FB
00AB8E
00BBA5
67D7C9
C6EFE9
E9F9F6

Requirements
Must have
Nice to have
Should not have

```html
<!DOCTYPE html>
<html lang="en">
<head>
<meta charset="utf-8">
<title>Brindle Forks — Real Food, Real Results</title>
<link rel="stylesheet" href="https://fonts.googleapis.com/css2?family=Josefin+Sans:wght@400;600;700&family=Poppins:wght@400;500;600&display=swap">
<style>
:root{
  --forest:#0e4a37;
  --forest-deep:#0a3d2e;
  --sage:#b4c6a6;
  --sage-soft:#e4eae2;
  --mint:#7cc39a;
  --tick:#2ea776;
  --ink:#1d1d1d;
  --body:#3b3b3b;
  --white:#ffffff;
}
*{box-sizing:border-box;margin:0;padding:0}
html,body{width:1200px;height:4532px;overflow:hidden;background:var(--white)}
body{position:relative;font-family:'Poppins',sans-serif;color:var(--body)}
.abs{position:absolute}
.head-font{font-family:'Josefin Sans',sans-serif}
.btn{position:absolute;display:flex;align-items:center;justify-content:center;background:var(--forest);color:var(--white);border-radius:30px;font-family:'Josefin Sans',sans-serif;font-weight:600}
.center{text-align:center}

/* hero */
.hero{position:absolute;left:0;top:0;width:1200px;height:960px}
.hero-photo{position:absolute;inset:0;background:
  radial-gradient(ellipse 300px 260px at 800px 420px,#e9b99b 0%,rgba(233,185,155,0) 70%),
  radial-gradient(ellipse 260px 150px at 600px 770px,#d9dfcf 0%,rgba(217,223,207,0) 75%),
  linear-gradient(90deg,#f2f5f3 0%,#e7ece9 35%,#d8dfe6 60%,#b9c9dc 80%,#d8e0ea 100%)}
.hero-shapes{position:absolute;left:0;top:0}
.brand{position:absolute;left:112px;top:44px;width:230px;text-align:center}
.brand-name{font-family:'Josefin Sans',sans-serif;font-weight:700;font-size:34px;color:var(--forest);line-height:1}
.brand-tag{font-size:9px;letter-spacing:3px;color:var(--forest);margin-top:10px}
.nav{position:absolute;top:64px;font-size:12px;color:var(--forest-deep)}
.nav span{position:absolute;white-space:nowrap}
.cart{position:absolute;left:922px;top:62px;font-size:11px;color:var(--forest-deep);display:flex;align-items:center;gap:6px}
.cart b{display:inline-flex;width:14px;height:14px;border-radius:50%;background:var(--forest);color:#fff;font-size:8px;align-items:center;justify-content:center;font-weight:500}
.login{left:1026px;top:55px;width:94px;height:33px;font-family:'Poppins',sans-serif;font-weight:500;font-size:14px}
.hero-welcome{position:absolute;left:121px;top:340px;font-size:56px;color:var(--forest);font-weight:400}
.hero-title{position:absolute;left:118px;top:418px;font-size:76px;font-weight:700;color:var(--forest-deep);letter-spacing:2px;white-space:nowrap}
.hero-sub{position:absolute;left:122px;top:512px;font-size:46px;color:var(--forest-deep)}
.hero-btn{left:120px;top:595px;width:156px;height:56px;font-size:21px}
.scroll-dot{position:absolute;left:565px;top:871px;width:70px;height:70px;border-radius:50%;background:#fff;box-shadow:0 4px 14px rgba(0,0,0,.18);display:flex;align-items:center;justify-content:center}

/* intro */
.intro-title{position:absolute;left:0;width:1200px;top:985px;font-size:41px;font-weight:700;color:#1b1b1b;line-height:52px}
.intro-text{position:absolute;left:240px;width:720px;top:1110px;font-size:15px;line-height:27px;color:#333}
.pill{position:absolute;top:1193px;height:62px;background:#fff;border-radius:6px;box-shadow:0 4px 16px rgba(0,0,0,.12);display:flex;align-items:center;justify-content:center;gap:16px;font-size:23px;color:#1d1d1d;font-weight:500}
.bowl{position:absolute;top:1290px;width:162px;height:118px;border-radius:50%}
.cart-btn{left:507px;top:1447px;width:165px;height:53px;font-size:20px}

/* vision */
.vision-top{position:absolute;left:0;top:1545px;width:700px;height:240px;background:var(--sage)}
.vision-bottom{position:absolute;left:0;top:1785px;width:700px;height:241px;background:var(--forest)}
.vm-title{position:absolute;font-size:40px;font-weight:700;width:560px;text-align:center}
.vm-text{position:absolute;width:380px;font-size:14.5px;line-height:26px;text-align:center}

/* stats */
.stats-title{position:absolute;left:0;width:1200px;top:2068px;font-size:40px;font-weight:600;color:#1b1b1b}
.stat{position:absolute;top:2160px;text-align:center;width:220px}
.stat-num{font-family:'Josefin Sans',sans-serif;font-weight:700;font-size:60px;color:#1b1b1b;line-height:70px}
.stat-label{font-size:22px;color:#1d1d1d;line-height:32px}

/* process */
.process{position:absolute;left:0;top:2341px;width:1200px}
.process-title{position:absolute;left:0;width:1200px;top:2380px;font-size:42px;font-weight:700;color:#fff}
.card-frame{position:absolute;border:1.5px solid #cfd9d2;border-radius:14px}
.card{position:absolute;background:#fff;border-radius:12px;text-align:center;padding:0 30px}
.card h3{font-family:'Poppins',sans-serif;font-weight:500;font-size:25px;color:var(--forest);line-height:38px;margin-top:50px}
.card p{font-size:16.5px;line-height:30px;color:#333;margin-top:20px}

/* values */
.values-title{position:absolute;left:0;width:1200px;top:3116px;font-size:42px;font-weight:700;color:#1b1b1b}
.values-text{position:absolute;left:0;width:1200px;top:3183px;font-size:17px;line-height:28px;color:#2a2a2a}
.meals-note{position:absolute;left:0;width:1200px;top:3290px;font-size:18px;font-weight:600;color:#1b1b1b}
.v-icon{position:absolute;top:3351px;width:116px;height:116px;border-radius:50%;border:3px solid var(--forest);display:flex;align-items:center;justify-content:center}
.v-icon i{width:96px;height:96px;border-radius:50%;background:var(--forest);display:flex;align-items:center;justify-content:center}
.v-label{position:absolute;top:3488px;width:200px;text-align:center;font-size:19px;font-weight:500;color:var(--forest)}

/* audience */
.who{position:absolute;left:0;top:3546px;width:1200px;height:613px;background:var(--sage-soft)}
.who-title{position:absolute;left:0;width:1200px;top:3578px;font-size:42px;font-weight:700;color:#1b1b1b}
.who-card{position:absolute;top:3661px;height:303px;border-radius:4px;text-align:center;color:#fff;padding:0 30px}
.who-card h4{font-family:'Poppins',sans-serif;font-weight:500;font-size:23px;margin-top:30px}
.who-card p{font-size:16px;line-height:25.5px;margin-top:14px;height:128px;overflow:hidden;color:#e8efe9}
.who-card .more{display:inline-flex;align-items:center;justify-content:center;width:104px;height:30px;border-radius:16px;font-size:11px;font-weight:500;margin-top:16px}
.who-note{position:absolute;left:0;width:1200px;top:3995px;font-size:17.5px;line-height:27px;color:#2a2a2a}
.menu-btn{left:484px;top:4069px;width:225px;height:48px;font-size:20px}

/* footer */
.footer{position:absolute;left:0;top:4159px;width:1200px;height:373px;background:var(--forest-deep);color:#fff}
.f-head{position:absolute;top:4224px;font-size:13px;text-decoration:underline;letter-spacing:.3px}
.f-row{position:absolute;font-size:13px;display:flex;align-items:center;gap:16px}
.f-ico{width:30px;height:30px;border-radius:50%;border:1.5px solid #fff;display:flex;align-items:center;justify-content:center}
.f-link{position:absolute;font-size:13px}
.f-link::before{content:"»";margin-right:14px}
.f-sep{position:absolute;top:4215px;width:1px;height:230px;background:rgba(255,255,255,.18)}
.social{position:absolute;top:4365px;width:38px;height:38px;border-radius:50%;border:1.5px solid #fff}
.pay{position:absolute;top:4421px;width:34px;height:20px;border-radius:3px;background:#fff}
.copy{position:absolute;left:0;width:1200px;top:4490px;font-size:12px;text-align:center}
</style>
</head>
<body>

<!-- HERO -->
<section class="hero">
  <div class="hero-photo" role="img" aria-label="Photo of a smiling woman eating a fresh salad with tomatoes and greens from a white bowl"></div>
  <svg class="hero-shapes" width="1200" height="960" viewBox="0 0 1200 960">
    <path d="M0 0H1200V108C1060 96 900 150 700 185C520 215 330 175 180 135C100 115 40 118 0 125Z" fill="#fff"/>
    <path d="M0 850C220 905 420 935 620 932C860 928 1050 860 1200 772V960H0Z" fill="#fff"/>
    <path d="M560 928C820 928 1030 862 1200 762V786C1040 872 830 938 560 934Z" fill="#b4c6a6"/>
    <path d="M0 790C110 815 240 870 345 922C230 905 110 885 0 878Z" fill="#0e4a37"/>
  </svg>

  <div class="brand">
    <div class="brand-name">Brindle Forks</div>
    <div class="brand-tag">EAT BETTER. LIVE BETTER.</div>
  </div>

  <nav class="nav">
    <span style="left:368px">MENU ▾</span>
    <span style="left:450px">ABOUT ▾</span>
    <span style="left:547px">PROGRAMS ▾</span>
    <span style="left:665px">SHOP NOW ▾</span>
    <span style="left:783px">FAQ</span>
  </nav>
  <div class="cart">
    <svg width="14" height="12" viewBox="0 0 14 12"><path d="M0 1H3L5 8H12L13.5 3H4" fill="none" stroke="#0a3d2e" stroke-width="1.4"/><circle cx="6" cy="10.5" r="1.1" fill="#0a3d2e"/><circle cx="11" cy="10.5" r="1.1" fill="#0a3d2e"/></svg>
    CART <b>0</b>
  </div>
  <div class="btn login">LOGIN</div>

  <div class="hero-welcome head-font">Welcome to</div>
  <div class="hero-title head-font">BRINDLE FORKS</div>
  <div class="hero-sub head-font">Real Food, Real Results</div>
  <div class="btn hero-btn">View Menu</div>

  <div class="scroll-dot">
    <svg width="18" height="28" viewBox="0 0 18 28"><rect x="1.5" y="1.5" width="15" height="25" rx="7.5" fill="none" stroke="#0e4a37" stroke-width="2"/><line x1="9" y1="7" x2="9" y2="12" stroke="#0e4a37" stroke-width="2" stroke-linecap="round"/></svg>
  </div>
</section>

<!-- INTRO -->
<h1 class="intro-title head-font center">Science Backed, Chef Prepared Meals…<br>Delivered Fresh</h1>
<p class="intro-text center">More than just a meal plan, we provide a sustainable diet &amp; nutritional support that empowers you to live your best life, no matter your health goals.</p>

<div class="pill" style="left:116px;width:252px">
  <svg width="26" height="26" viewBox="0 0 26 26"><circle cx="13" cy="13" r="11" fill="none" stroke="#2ea776" stroke-width="2.4"/><path d="M8 13.5L11.5 17L19 9" fill="none" stroke="#2ea776" stroke-width="2.6"/></svg>Weight Loss
</div>
<div class="pill" style="left:400px;width:267px">
  <svg width="26" height="26" viewBox="0 0 26 26"><circle cx="13" cy="13" r="11" fill="none" stroke="#2ea776" stroke-width="2.4"/><path d="M8 13.5L11.5 17L19 9" fill="none" stroke="#2ea776" stroke-width="2.6"/></svg>Health Issues
</div>
<div class="pill" style="left:699px;width:383px">
  <svg width="26" height="26" viewBox="0 0 26 26"><circle cx="13" cy="13" r="11" fill="none" stroke="#2ea776" stroke-width="2.4"/><path d="M8 13.5L11.5 17L19 9" fill="none" stroke="#2ea776" stroke-width="2.6"/></svg>Improved Performance
</div>

<div class="bowl" role="img" aria-label="Plated meal of grilled fish with broccoli and peppers" style="left:297px;background:radial-gradient(circle at 50% 45%,#b98a4a 0%,#6f8c3c 45%,#e2e4e6 72%,#c9cdd1 100%)"></div>
<div class="bowl" role="img" aria-label="Bowl of colourful salad with grains and greens" style="left:509px;background:radial-gradient(circle at 50% 45%,#d4873b 0%,#6ea04a 45%,#e2e4e6 72%,#c9cdd1 100%)"></div>
<div class="bowl" role="img" aria-label="Bowl of roasted sweet potato with beets and peas" style="left:721px;background:radial-gradient(circle at 50% 45%,#e0953a 0%,#8a4a5c 35%,#7aa544 52%,#e2e4e6 72%,#c9cdd1 100%)"></div>

<div class="btn cart-btn">Add To Cart</div>

<!-- VISION & MISSION -->
<div class="vision-top"></div>
<div class="vision-bottom"></div>
<svg class="abs" style="left:0;top:1545px" width="1200" height="481" viewBox="0 0 1200 481" role="img" aria-label="Photo of a chef seasoning a tray of roasted vegetables">
  <defs>
    <linearGradient id="chefPhoto" x1="0" y1="0" x2="1" y2="1">
      <stop offset="0" stop-color="#2e3f5a"/>
      <stop offset=".45" stop-color="#3a4c63"/>
      <stop offset=".75" stop-color="#8a5a3a"/>
      <stop offset="1" stop-color="#c2532e"/>
    </linearGradient>
  </defs>
  <path d="M585 0C560 40 580 80 620 110C660 140 650 190 610 230C570 270 545 310 580 360C610 405 600 450 570 481H1200V0Z" fill="url(#chefPhoto)"/>
  <path d="M580 0C556 40 575 82 612 112C652 142 642 190 602 230" fill="none" stroke="#0e4a37" stroke-width="10"/>
</svg>

<h2 class="vm-title head-font" style="left:67px;top:1582px;color:#1b1b1b">Our Vision</h2>
<p class="vm-text" style="left:164px;top:1640px;color:#1d1d1d">A world of healthy and happy people. Brindle Forks develops new food based on the latest science to provide the human body with the proper nutrients for optimal health.</p>
<h2 class="vm-title head-font" style="left:62px;top:1812px;color:#fff">Our Mission</h2>
<p class="vm-text" style="left:159px;top:1868px;color:#fff">Empower every person to utilize food as a means of living a healthy life. Brindle Forks develops new food based on the latest science to provide the human body with the proper nutrients for optimal health.</p>

<!-- STATS -->
<h2 class="stats-title head-font center">Award Winning Meals</h2>
<div class="stat" style="left:151px"><div class="stat-num">150K</div><div class="stat-label">Happy Clients</div></div>
<div class="stat" style="left:400px;top:2165px"><div class="stat-num">500K</div><div class="stat-label">Meals Served<br>Nation Wide</div></div>
<div class="stat" style="left:638px;top:2168px"><div class="stat-num">35+</div><div class="stat-label">Chef Prepared<br>Meals</div></div>
<div class="stat" style="left:845px;top:2168px"><div class="stat-num">215</div><div class="stat-label">Awards</div></div>

<!-- PROCESS -->
<svg class="process" width="1200" height="745" viewBox="0 0 1200 745">
  <path d="M0 0H1200V690C1050 640 900 640 780 680C650 725 560 740 470 720C330 690 160 640 0 680Z" fill="#0e4a37"/>
</svg>
<h2 class="process-title head-font center">Enjoy The Process Of Becoming A Better You!</h2>
<svg class="abs" style="left:0;top:2470px" width="420" height="440" viewBox="0 0 420 440">
  <circle cx="264" cy="293" r="141" fill="#b4c6a6"/>
  <circle cx="170" cy="205" r="172" fill="none" stroke="#b4c6a6" stroke-width="1.5"/>
</svg>
<div class="abs" role="img" aria-label="Top view of a healthy bowl with avocado, greens, grains and radish" style="left:18px;top:2522px;width:300px;height:300px;border-radius:50%;background:radial-gradient(circle at 55% 50%,#8fbf4a 0%,#b9486e 35%,#d9794a 55%,#a89a74 75%,#e9ece8 90%)"></div>

<div class="card-frame" style="left:461px;top:2527px;width:333px;height:368px"></div>
<div class="card" style="left:431px;top:2540px;width:345px;height:339px">
  <h3>FRESH MEALS<br>DELIVERED WEEKLY</h3>
  <p>Eating properly is no longer difficult. We've handcrafted delicious meals that are results driven, so all you need to do is, enjoy.</p>
</div>
<div class="card-frame" style="left:847px;top:2527px;width:330px;height:368px"></div>
<div class="card" style="left:815px;top:2540px;width:345px;height:339px">
  <h3>LIFE CHANGING<br>RESULTS</h3>
  <p>No matter your situation, we can help. Our dietician designed meals focus on an anti-inflammatory diet, which is the foundation to good health.</p>
</div>

<!-- VALUES -->
<h2 class="values-title head-font center">Value Propositions</h2>
<p class="values-text center">We Educate &amp; Empower People Through Food to Live Their Best Life<br>Sustainable health through proper nutrition… that’s enjoyable too.<br>Order online for nationwide delivery! It's that simple! Eat Better. Live Better.</p>
<p class="meals-note center">ALL OUR MEALS AND SNACKS ARE:</p>

<div class="v-icon" style="left:317px"><i>
  <svg width="54" height="54" viewBox="0 0 54 54"><path d="M12 42C12 22 26 12 44 10C44 30 32 42 14 42Z" fill="#fff"/><path d="M10 46C18 34 26 26 36 20" stroke="#0e4a37" stroke-width="2.5" fill="none"/></svg>
</i></div>
<div class="v-icon" style="left:532px"><i>
  <svg width="54" height="54" viewBox="0 0 54 54"><line x1="14" y1="44" x2="38" y2="12" stroke="#fff" stroke-width="3"/><ellipse cx="30" cy="18" rx="4" ry="7" fill="#fff" transform="rotate(38 30 18)"/><ellipse cx="24" cy="26" rx="4" ry="7" fill="#fff" transform="rotate(38 24 26)"/><circle cx="36" cy="38" r="9" fill="none" stroke="#fff" stroke-width="3"/><line x1="30" y1="44" x2="42" y2="32" stroke="#fff" stroke-width="3"/></svg>
</i></div>
<div class="v-icon" style="left:744px"><i>
  <svg width="54" height="54" viewBox="0 0 54 54"><path d="M27 8C20 20 14 28 14 35A13 13 0 0 0 40 35C40 28 34 20 27 8Z" fill="#fff"/><path d="M20 36A7 7 0 0 0 27 43" stroke="#0e4a37" stroke-width="2.5" fill="none"/></svg>
</i></div>
<div class="v-label" style="left:275px">SUGAR FREE</div>
<div class="v-label" style="left:490px">GLUTEN FREE</div>
<div class="v-label" style="left:702px">DAIRY FREE</div>

<!-- AUDIENCE -->
<section class="who"></section>
<h2 class="who-title head-font center">Who Is Brindle Forks For ?</h2>

<div class="who-card" role="img" aria-label="Green tinted photo of a person living a healthy lifestyle" style="left:51px;width:266px;background:linear-gradient(160deg,#2f6e55 0%,#174c3a 55%,#0d3a2b 100%)">
  <h4>General Health</h4>
  <p>You need the support of a healthy diet to get back in shape and improve your overall health. Having a meal plan that supports you</p>
  <span class="more" style="background:var(--mint)">LEARN MORE</span>
</div>
<div class="who-card" role="img" aria-label="Green tinted photo of a fitness enthusiast training" style="left:329px;width:264px;background:linear-gradient(160deg,#3d8a68 0%,#23684d 55%,#14503b 100%)">
  <h4>Fitness Enthusiasts</h4>
  <p>You eat clean, fitness &amp; eating right are a huge part of your life. Enjoy healthy meal delivery to keep yourself on track.health. Having a</p>
  <span class="more" style="background:var(--forest-deep)">LEARN MORE</span>
</div>
<div class="who-card" role="img" aria-label="Green tinted photo of a busy professional at work" style="left:605px;width:264px;background:linear-gradient(160deg,#2b6651 0%,#174c3a 55%,#0c3628 100%)">
  <h4>Business Individuals</h4>
  <p>You have a growing to-do list that never seems to end. No time to do healthy meal prep. You prefer a healthy meal over a fast food di-</p>
  <span class="more" style="background:var(--mint)">LEARN MORE</span>
</div>
<div class="who-card" role="img" aria-label="Green tinted photo of a professional athlete" style="left:883px;width:266px;background:linear-gradient(160deg,#3f8c6a 0%,#246a4f 55%,#14503b 100%)">
  <h4>Professional Athletes</h4>
  <p>You refuse to accept anything less than the best when it comes to nutrition, increasing your performance doesn't just stop at the gym. En-</p>
  <span class="more" style="background:var(--forest-deep)">LEARN MORE</span>
</div>

<p class="who-note center">Brindle Forks goal is to provide nutrient rich, fully prepared food with the<br>belief that if you eat better you live better.</p>
<div class="btn menu-btn">Check Out The Menu</div>

<!-- FOOTER -->
<footer class="footer"></footer>
<div class="abs" style="left:142px;top:4240px;width:220px;text-align:center;color:#fff">
  <div style="font-family:'Josefin Sans',sans-serif;font-weight:700;font-size:30px;line-height:1">Brindle Forks</div>
  <div style="font-size:9px;letter-spacing:3px;margin-top:24px">EAT BETTER. LIVE BETTER.</div>
</div>
<div class="social" style="left:178px"></div>
<div class="social" style="left:229px"></div>
<div class="social" style="left:282px"></div>
<div class="pay" style="left:169px"></div>
<div class="pay" style="left:208px"></div>
<div class="pay" style="left:247px"></div>
<div class="pay" style="left:286px"></div>

<div class="f-head" style="left:445px;color:#fff">CONTACT US</div>
<div class="f-row" style="left:445px;top:4272px;color:#fff">
  <span class="f-ico"><svg width="14" height="14" viewBox="0 0 14 14"><path d="M3 1L5 4L4 5.5C5 7.5 6.5 9 8.5 10L10 9L13 11L11.5 13C6 13 1 8 1 2.5Z" fill="#fff"/></svg></span>855-410-2738
</div>
<div class="f-row" style="left:445px;top:4334px;color:#fff">
  <span class="f-ico"><svg width="14" height="12" viewBox="0 0 14 12"><rect x="1" y="1.5" width="12" height="9" rx="1" fill="none" stroke="#fff" stroke-width="1.3"/><path d="M1.5 2L7 7L12.5 2" fill="none" stroke="#fff" stroke-width="1.3"/></svg></span>nora@brindleforks.com
</div>
<div class="f-row" style="left:445px;top:4396px;color:#fff">
  <span class="f-ico"><svg width="14" height="14" viewBox="0 0 14 14"><circle cx="7" cy="7" r="5.8" fill="none" stroke="#fff" stroke-width="1.3"/><ellipse cx="7" cy="7" rx="2.6" ry="5.8" fill="none" stroke="#fff" stroke-width="1.1"/><line x1="1.2" y1="7" x2="12.8" y2="7" stroke="#fff" stroke-width="1.1"/></svg></span>www.brindleforks.com
</div>

<div class="f-sep" style="left:686px"></div>
<div class="f-sep" style="left:920px"></div>

<div class="f-head" style="left:745px;color:#fff">QUICKLINKS</div>
<div class="f-link" style="left:728px;top:4262px;color:#fff">My Account</div>
<div class="f-link" style="left:728px;top:4299px;color:#fff">Shipping &amp; Returns</div>
<div class="f-link" style="left:728px;top:4336px;color:#fff">Gift Certificates</div>
<div class="f-link" style="left:728px;top:4373px;color:#fff">Become an Affiliate</div>
<div class="f-link" style="left:728px;top:4410px;color:#fff">Corporate Catering</div>

<div class="f-head" style="left:982px;color:#fff">OTHERLINKS</div>
<div class="f-link" style="left:958px;top:4262px;color:#fff">Privacy Policy</div>
<div class="f-link" style="left:958px;top:4292px;color:#fff">Order Status</div>
<div class="f-link" style="left:958px;top:4322px;color:#fff">View Cart</div>
<div class="f-link" style="left:958px;top:4352px;color:#fff">All Products</div>
<div class="f-link" style="left:958px;top:4382px;color:#fff">Testimonials</div>
<div class="abs" style="left:983px;top:4412px;font-size:13px;color:#fff">Podcast</div>

<div class="copy">2022 brindle forks. All Rights Reserved</div>

</body>
</html>
```